High-Converting Facebook Ads for Portals Drapes & Louvres (6 Products)

We are looking for a graphic designer to create high-quality Facebook & Instagram ads for our business: Portals Drapes and Louvres (Melbourne, Australia).

We require 6 separate ad designs, each for a different product:

Zipscreen Blinds

Outdoor Awnings

Plantation Shutters

Roller Shutters

Security Doors

Roller Blinds & Sheer Curtains

Ad Specifications:

Sizes:

1440 x 1800 px (4:5 ratio)

1080 x 1080 px (1:1 ratio)

1080 x 1920 px (9:16 ratio for Stories/Reels)

Format: PNG (high resolution, not blurry)

Designed specifically for Meta (Facebook/Instagram ads)

Mobile-friendly layout (clear, easy to read)

Style:

Bold, sales-driven, retail-style ads (NOT minimal)

Eye-catching and designed to generate leads

Clean, professional layout

Similar to promotional home improvement ads

Brand Colours:

Red: #E31E24

Blue: #0072BC

White backgrounds

Each ad must include:

“SALE NOW ON” banner at top

Our showroom address:
482 Upper Wattleby Road, Kestrel Heights (must be fully visible, not cut off)

Phone number: 9471 2658

Our logo (provided)

Badge: “Celebrating 13 YEARS in Business” (must be clean and readable)

Call to Action:

For 5 ads: “Book a FREE quote TODAY!”

For Security Doors ad: “ORDER NOW”

Offers / Pricing:

Most products: “UP TO 40% OFF”

Plantation Shutters: “FROM $299/sqm”

Security Doors: “FROM $750”

Content for each ad (examples):

Zipscreen Blinds:

Made to Measure

Fully Installed

Wind, Sun & Insect Protection

Outdoor Awnings:

Reduce Heat & Glare

Energy Saving

Custom Made

Plantation Shutters:

Modern & Elegant

Light & Privacy Control

Durable & Easy Care

Roller Shutters:

Security Protection

Block Heat & Noise

Total Light Control

Security Doors:

3 Point Locking

Premium Mesh

Custom Made

Blinds & Sheers:

Huge Range of Fabrics

Modern Soft Finish

Perfect for Any Room

Important Notes:

All text must be sharp and easy to read (no blur)

Layout must be balanced and not overcrowded

Ensure no text is cut off (especially address and headings)

Badge text must be straight and professional (no distortion)

Use high-quality, relevant images (we will provide references)

Goal:
Create ads that look professional, trustworthy, and generate enquiries/bookings for in-home quotes.

We are open to creative ideas but want a strong, bold retail-style ad that converts.
I have uploaed chatgpt mocks

Target Market(s)

Homeowners in Melbourne, Australia (typically aged 30–65) looking to improve their homes with blinds, shutters, awnings and security doors. Mid to high income households focused on quality, security, and modern home upgrades.

Industry/Entity Type

Home Improvement / Construction / Retail

Font styles to use
Sans Serif

Requirements
Must have
• Clear, bold and easy-to-read text (must be readable on mobile) High-quality, non-blurry design Strong “SALE” style layout (retail promotional look) Proper spacing (no overcrowded designs) All key info visible (address must NOT be cut off) Correct pricing and offers included Clean “13 YEARS” badge (no distortion or curved text) Consistent branding across all 6 ads
Nice to have
• Modern, slightly premium feel while still being bold Good use of contrast (red/blue/white) Subtle shadows or layering to improve depth Clean use of icons or bullet points Strong hierarchy (headline → benefits → offer → CTA) Variations in layout for testing different ad styles
Should not have
• Minimal or plain designs (we want bold, sales-driven ads) Hard-to-read fonts or script fonts Low-quality or blurry images Overcrowded layouts with too much text Important text cut off (especially address or headings) Overuse of effects or “cheap” looking graphics Yellow-heavy colour schemes (must follow brand colours)

```html
<!DOCTYPE html>
<html lang="en">
<head>
<meta charset="utf-8">
<title>Portals Drapes &amp; Louvres – Sale Ads 1440 x 1800</title>
<link rel="stylesheet" href="https://fonts.googleapis.com/css2?family=Poppins:wght@300;500;600;700;800&family=Oswald:wght@500;600&family=Playfair+Display:wght@700;900&display=swap">
<style>
:root{
  --red:#E31E24;
  --blue:#0072BC;
  --blue-deep:#0a5fa3;
  --white:#ffffff;
  --board:#333333;
  --label:#b9b4b4;
  --gold:#d4a62a;
  --gold-light:#f0cf6a;
  --gold-dark:#8a6512;
  --ink:#1d1d1d;
}
*{box-sizing:border-box;margin:0;padding:0}
html,body{width:1200px;height:1200px;overflow:hidden;background:var(--board)}
body{position:relative;font-family:"Poppins",sans-serif}

.board__label{position:absolute;top:44px;left:0;width:1200px;text-align:center;
  font:300 43px/1 "Poppins",sans-serif;color:var(--label);letter-spacing:1px}

.ad{position:absolute;width:345px;height:432px;overflow:hidden;background:var(--white)}
.ad--zip{left:47px;top:153px}
.ad--awning{left:427px;top:153px}
.ad--plantation{left:807px;top:153px}
.ad--roller{left:47px;top:615px}
.ad--security{left:427px;top:615px}
.ad--sheer{left:807px;top:615px}

/* header */
.ad__head{position:absolute;left:0;top:0;width:345px;height:68px;background:var(--white);
  display:flex;align-items:center;padding:10px 6px 0 8px;z-index:3}
.brand{display:flex;align-items:center;gap:3px;width:80px;flex:none}
.brand__mark{width:9px;height:9px;background:var(--red);flex:none}
.brand__name{font:700 8px/1.1 "Poppins",sans-serif;color:var(--blue)}
.ad__headline{font:800 33px/1 "Poppins",sans-serif;color:var(--blue);letter-spacing:-.6px;white-space:nowrap;margin-left:2px}

/* photo */
.ad__photo{position:absolute;left:0;top:68px;width:345px;height:250px;z-index:0}
.ad--zip .ad__photo{height:364px;background:linear-gradient(120deg,#d9dde0 0%,#9a5a45 30%,#2b2b2d 45%,#2b2b2d 70%,#a4523b 80%,#2a2a2a 100%)}
.ad--awning .ad__photo{height:242px;background:linear-gradient(160deg,#4d6b55 0%,#e8e8e2 18%,#7b3a2c 38%,#9b4b39 60%,#6f7f4f 85%,#5a5a4a 100%)}
.ad--plantation .ad__photo{height:242px;background:linear-gradient(180deg,#e9ecef 0%,#c7ccd0 35%,#f4f4f2 55%,#9aa0a6 85%,#555 100%)}
.ad--roller .ad__photo{height:249px;background:linear-gradient(100deg,#2d2f31 0%,#6c6a66 28%,#d7d7d4 45%,#c59a6e 75%,#a9b0b4 100%)}
.ad--security .ad__photo{height:249px;background:linear-gradient(90deg,#f1f0ed 0%,#e6e5e1 50%,#3a3d44 58%,#3a3d44 82%,#e2e1de 90%,#f3f2ef 100%)}
.ad--sheer .ad__photo{height:249px;background:linear-gradient(90deg,#e8e8e6 0%,#8b8176 18%,#6e655c 40%,#9a8f82 60%,#7a7065 80%,#eeeeec 100%)}

/* address & phone bands */
.ad__address{position:absolute;left:16px;top:68px;width:329px;height:25px;background:var(--red);
  clip-path:polygon(0 0,100% 0,98% 100%,4% 100%);display:flex;align-items:center;justify-content:center;gap:5px;
  font:600 12.5px/1 "Poppins",sans-serif;color:var(--white);z-index:3;white-space:nowrap}
.ad__phone{position:absolute;height:26px;background:var(--blue);
  clip-path:polygon(0 0,100% 0,96% 100%,4% 100%);display:flex;align-items:center;justify-content:center;gap:8px;
  font:700 21px/1 "Poppins",sans-serif;color:var(--white);z-index:3;letter-spacing:.3px}
.ad--zip .ad__phone{left:34px;top:101px;width:211px}
.ad--awning .ad__phone,.ad--plantation .ad__phone{left:174px;top:100px;width:162px;font-size:19px}
.ad--roller .ad__phone,.ad--security .ad__phone,.ad--sheer .ad__phone{left:14px;top:99px;width:200px}
.icon{width:12px;height:12px;flex:none}

/* badge */
.badge{position:absolute;width:88px;height:88px;border-radius:50%;z-index:4;
  background:radial-gradient(circle at 35% 30%,var(--gold-light),var(--gold) 55%,var(--gold-dark) 100%);
  border:2px solid #fff3c4;box-shadow:0 2px 5px rgba(0,0,0,.35);
  display:flex;flex-direction:column;align-items:center;justify-content:center;color:var(--ink);text-align:center}
.badge__top{font:700 5.5px/1 "Poppins",sans-serif;letter-spacing:.2px}
.badge__num{font:900 34px/.95 "Playfair Display",serif}
.badge__years{font:700 10px/1 "Playfair Display",serif;letter-spacing:.5px}
.badge__bottom{font:600 5.5px/1.4 "Poppins",sans-serif;letter-spacing:1.2px}
.ad--zip .badge{left:4px;top:132px}
.ad--awning .badge,.ad--plantation .badge{left:94px;top:95px}
.ad--roller .badge{left:221px;top:96px}
.ad--security .badge,.ad--sheer .badge{left:7px;top:127px}

/* call to action */
.cta{position:absolute;z-index:4;display:flex;flex-direction:column;align-items:center;justify-content:center;
  border-radius:22px;color:var(--white);text-align:center;font:700 11px/1.35 "Poppins",sans-serif;
  box-shadow:0 2px 4px rgba(0,0,0,.25);background:var(--red)}
.ad--zip .cta{left:3px;top:273px;width:131px;height:32px;font-size:10px;line-height:1.3}
.ad--awning .cta{left:26px;top:236px;width:293px;height:81px;font-size:24px;line-height:1.25;border-radius:24px}
.ad--plantation .cta{left:78px;top:247px;width:177px;height:46px;font-size:13px}
.ad--roller .cta{left:77px;top:247px;width:177px;height:47px;font-size:13.5px;background:var(--blue)}
.ad--security .cta{left:2px;top:255px;width:177px;height:46px;font-size:19px}
.ad--sheer .cta{left:7px;top:277px;width:325px;height:46px;font-size:20px}

/* lower panel */
.ad__panel{position:absolute;left:0;width:345px;z-index:2;color:var(--white)}
.ad--zip .ad__panel{top:300px;height:132px;background:linear-gradient(25deg,rgba(0,114,188,.95) 0%,rgba(0,114,188,.85) 50%,rgba(0,114,188,0) 72%)}
.ad--awning .ad__panel,.ad--plantation .ad__panel{top:310px;height:122px;background:linear-gradient(160deg,var(--blue) 0%,var(--blue) 55%,var(--blue-deep) 100%)}
.ad--roller .ad__panel,.ad--security .ad__panel{top:317px;height:115px;background:var(--blue)}
.ad--sheer .ad__panel{top:317px;height:115px;background:linear-gradient(160deg,var(--blue) 0%,var(--blue) 50%,var(--blue-deep) 100%)}
.panel__split{position:absolute;top:0;right:0;width:192px;height:100%;background:var(--red);
  clip-path:polygon(0 0,100% 0,100% 100%,18% 100%);border-left:0}
.panel__split::before{content:"";position:absolute;inset:0}
.ad--roller .panel__edge,.ad--security .panel__edge{position:absolute;top:0;right:188px;width:40px;height:100%;
  background:var(--white);clip-path:polygon(0 0,8% 0,100% 100%,92% 100%)}

.product__title{position:absolute;font:600 19px/1 "Oswald",sans-serif;letter-spacing:-.2px;white-space:nowrap}
.benefits{position:absolute;list-style:none}
.benefits li{position:relative;padding-left:18px;font:600 11.5px/1 "Poppins",sans-serif;margin-bottom:6.5px;white-space:nowrap}
.benefits li::before{content:"";position:absolute;left:0;top:-1px;width:11px;height:11px;border:1.3px solid var(--white);border-radius:50%}
.benefits li::after{content:"";position:absolute;left:3.5px;top:1px;width:3px;height:6px;border:solid var(--white);border-width:0 1.6px 1.6px 0;transform:rotate(40deg)}

.ad--zip .product__title{left:12px;top:176px - 0;top:176px}
.ad--zip .product__title{top:176px}
.ad--zip .product__title{left:12px;top:174px}
.ad--zip .product__title{top:174px}
.ad--zip .product__title{top:174px}
.ad--zip .product__title{top:174px}
.ad--zip .product__title{top:174px}
.ad--zip .product__title{top:174px}
.ad--zip .product__title{top:174px}
.ad--zip .product__title{top:174px}

.ad--zip .product__title{top:23px}
.ad--zip .benefits{left:14px;top:61px}
.ad--awning .product__title,.ad--plantation .product__title{left:12px;top:21px}
.ad--awning .benefits,.ad--plantation .benefits{left:14px;top:56px}
.ad--roller .product__title,.ad--security .product__title,.ad--sheer .product__title{left:19px;top:20px}
.ad--roller .benefits,.ad--security .benefits,.ad--sheer .benefits{left:21px;top:55px}

/* offers */
.offer{position:absolute;z-index:3;color:var(--white);font-family:"Poppins",sans-serif;line-height:1}
.offer__lead{display:block;font-weight:500;font-size:27px}
.offer__value{display:block;font-weight:800;font-size:40px;letter-spacing:-.5px}
.offer__unit{font-weight:500;font-size:27px}
.ad--awning .offer{left:180px;top:20px}
.ad--awning .offer__value{margin-top:12px}
.ad--plantation .offer{left:200px;top:16px}
.ad--plantation .offer__lead{font-size:19px}
.ad--plantation .offer__value{font-size:33px;margin-top:7px}
.ad--plantation .offer__unit{display:block;font-size:29px;margin-top:2px}
.ad--roller .offer{left:186px;top:16px}
.ad--roller .offer__value{margin-top:8px}
.ad--security .offer{left:205px;top:18px}
.ad--security .offer__lead{font-size:23px}
.ad--security .offer__value{font-size:40px;margin-top:10px}
.ad--sheer .offer{left:205px;top:20px}
.ad--sheer .offer__lead{font-size:23px}
.ad--sheer .offer__value{font-size:31px;margin-top:10px}

.offer--stacked{position:absolute;left:155px;top:208px;z-index:3;font:700 28px/36px "Poppins",sans-serif}
.offer--stacked .blue{color:var(--blue);display:block}
.offer--stacked .red{color:var(--red);display:block}
</style>
</head>
<body>

<p class="board__label">1440 x 1800</p>

<!-- Zipscreen Blinds -->
<article class="ad ad--zip">
  <div class="ad__photo" role="img" aria-label="Brick house with dark zipscreen blinds lowered on the outdoor area"></div>
  <header class="ad__head">
    <div class="brand"><span class="brand__mark"></span><span class="brand__name">Portals Drapes<br>&amp; Louvres</span></div>
    <h2 class="ad__headline">SALE NOW ON</h2>
  </header>
  <p class="ad__address"><svg class="icon" viewBox="0 0 12 12"><circle cx="6" cy="6" r="6" fill="#fff"/><path d="M6 2.5a2 2 0 0 0-2 2c0 1.6 2 4 2 4s2-2.4 2-4a2 2 0 0 0-2-2z" fill="#E31E24"/></svg>482 Upper Wattleby Road, Kestrel Heights</p>
  <p class="ad__phone"><svg class="icon" viewBox="0 0 12 12"><circle cx="6" cy="6" r="6" fill="#fff"/><path d="M4 3.2l1 1.4-.6.7a4 4 0 0 0 2.3 2.3l.7-.6 1.4 1-.6 1A5.5 5.5 0 0 1 3 4z" fill="#0072BC"/></svg>9471 2658</p>
  <div class="badge"><span class="badge__top">CELEBRATING</span><span class="badge__num">13</span><span class="badge__years">YEARS</span><span class="badge__bottom">IN BUSINESS</span></div>
  <p class="offer--stacked"><span class="blue">UP</span><span class="blue">TO</span><span class="red">40%</span><span class="red">OFF</span></p>
  <p class="cta">Book a<br>FREE quote TODAY!”</p>
  <section class="ad__panel">
    <h3 class="product__title">ZIPSCREEN BLINDS:</h3>
    <ul class="benefits"><li>Made to Measure</li><li>Fully Installed</li><li>Wind, Sun &amp; Insect Protection</li></ul>
  </section>
</article>

<!-- Outdoor Awnings -->
<article class="ad ad--awning">
  <div class="ad__photo" role="img" aria-label="Brick home with striped outdoor awnings over the windows"></div>
  <header class="ad__head">
    <div class="brand"><span class="brand__mark"></span><span class="brand__name">Portals Drapes<br>&amp; Louvres</span></div>
    <h2 class="ad__headline">SALE NOW ON</h2>
  </header>
  <p class="ad__address"><svg class="icon" viewBox="0 0 12 12"><circle cx="6" cy="6" r="6" fill="#fff"/><path d="M6 2.5a2 2 0 0 0-2 2c0 1.6 2 4 2 4s2-2.4 2-4a2 2 0 0 0-2-2z" fill="#E31E24"/></svg>482 Upper Wattleby Road, Kestrel Heights</p>
  <p class="ad__phone"><svg class="icon" viewBox="0 0 12 12"><circle cx="6" cy="6" r="6" fill="#fff"/><path d="M4 3.2l1 1.4-.6.7a4 4 0 0 0 2.3 2.3l.7-.6 1.4 1-.6 1A5.5 5.5 0 0 1 3 4z" fill="#0072BC"/></svg>9471 2658</p>
  <div class="badge"><span class="badge__top">CELEBRATING</span><span class="badge__num">13</span><span class="badge__years">YEARS</span><span class="badge__bottom">IN BUSINESS</span></div>
  <p class="cta">Book a<br>FREE quote TODAY!”</p>
  <section class="ad__panel">
    <h3 class="product__title">OUTDOOR AWNINGS:</h3>
    <ul class="benefits"><li>Reduce Heat &amp; Glare</li><li>Energy Saving</li><li>Custom Made</li></ul>
    <p class="offer"><span class="offer__lead">UP TO</span><span class="offer__value">40% <span class="offer__unit">OFF</span></span></p>
  </section>
</article>

<!-- Plantation Shutters -->
<article class="ad ad--plantation">
  <div class="ad__photo" role="img" aria-label="Bright bedroom with white plantation shutters on the windows"></div>
  <header class="ad__head">
    <div class="brand"><span class="brand__mark"></span><span class="brand__name">Portals Drapes<br>&amp; Louvres</span></div>
    <h2 class="ad__headline">SALE NOW ON</h2>
  </header>
  <p class="ad__address"><svg class="icon" viewBox="0 0 12 12"><circle cx="6" cy="6" r="6" fill="#fff"/><path d="M6 2.5a2 2 0 0 0-2 2c0 1.6 2 4 2 4s2-2.4 2-4a2 2 0 0 0-2-2z" fill="#E31E24"/></svg>482 Upper Wattleby Road, Kestrel Heights</p>
  <p class="ad__phone"><svg class="icon" viewBox="0 0 12 12"><circle cx="6" cy="6" r="6" fill="#fff"/><path d="M4 3.2l1 1.4-.6.7a4 4 0 0 0 2.3 2.3l.7-.6 1.4 1-.6 1A5.5 5.5 0 0 1 3 4z" fill="#0072BC"/></svg>9471 2658</p>
  <div class="badge"><span class="badge__top">CELEBRATING</span><span class="badge__num">13</span><span class="badge__years">YEARS</span><span class="badge__bottom">IN BUSINESS</span></div>
  <p class="cta">Book a<br>FREE quote TODAY!”</p>
  <section class="ad__panel">
    <h3 class="product__title">PLANTATION SHUTTERS:</h3>
    <ul class="benefits"><li>Modern &amp; Elegant</li><li>Light &amp; Privacy Control</li><li>Durable &amp; Easy Care</li></ul>
    <p class="offer"><span class="offer__lead">FROM</span><span class="offer__value">$299</span><span class="offer__unit">/sqm</span></p>
  </section>
</article>

<!-- Roller Shutters -->
<article class="ad ad--roller">
  <div class="ad__photo" role="img" aria-label="Modern brick home front with grey roller shutters on the windows"></div>
  <header class="ad__head">
    <div class="brand"><span class="brand__mark"></span><span class="brand__name">Portals Drapes<br>&amp; Louvres</span></div>
    <h2 class="ad__headline">SALE NOW ON</h2>
  </header>
  <p class="ad__address"><svg class="icon" viewBox="0 0 12 12"><circle cx="6" cy="6" r="6" fill="#fff"/><path d="M6 2.5a2 2 0 0 0-2 2c0 1.6 2 4 2 4s2-2.4 2-4a2 2 0 0 0-2-2z" fill="#E31E24"/></svg>482 Upper Wattleby Road, Kestrel Heights</p>
  <p class="ad__phone"><svg class="icon" viewBox="0 0 12 12"><circle cx="6" cy="6" r="6" fill="#fff"/><path d="M4 3.2l1 1.4-.6.7a4 4 0 0 0 2.3 2.3l.7-.6 1.4 1-.6 1A5.5 5.5 0 0 1 3 4z" fill="#0072BC"/></svg>9471 2658</p>
  <div class="badge"><span class="badge__top">CELEBRATING</span><span class="badge__num">13</span><span class="badge__years">YEARS</span><span class="badge__bottom">IN BUSINESS</span></div>
  <p class="cta">Book a<br>FREE quote TODAY!”</p>
  <section class="ad__panel">
    <div class="panel__split"></div>
    <h3 class="product__title">ROLLER SHUTTERS:</h3>
    <ul class="benefits"><li>Security Protection</li><li>Block Heat &amp; Noise</li><li>Total Light Control</li></ul>
    <p class="offer"><span class="offer__lead">UP TO</span><span class="offer__value">40% <span class="offer__unit">OFF</span></span></p>
  </section>
</article>

<!-- Security Doors -->
<article class="ad ad--security">
  <div class="ad__photo" role="img" aria-label="Dark grey security mesh door set in a white rendered wall"></div>
  <header class="ad__head">
    <div class="brand"><span class="brand__mark"></span><span class="brand__name">Portals Drapes<br>&amp; Louvres</span></div>
    <h2 class="ad__headline">SALE NOW ON</h2>
  </header>
  <p class="ad__address"><svg class="icon" viewBox="0 0 12 12"><circle cx="6" cy="6" r="6" fill="#fff"/><path d="M6 2.5a2 2 0 0 0-2 2c0 1.6 2 4 2 4s2-2.4 2-4a2 2 0 0 0-2-2z" fill="#E31E24"/></svg>482 Upper Wattleby Road, Kestrel Heights</p>
  <p class="ad__phone"><svg class="icon" viewBox="0 0 12 12"><circle cx="6" cy="6" r="6" fill="#fff"/><path d="M4 3.2l1 1.4-.6.7a4 4 0 0 0 2.3 2.3l.7-.6 1.4 1-.6 1A5.5 5.5 0 0 1 3 4z" fill="#0072BC"/></svg>9471 2658</p>
  <div class="badge"><span class="badge__top">CELEBRATING</span><span class="badge__num">13</span><span class="badge__years">YEARS</span><span class="badge__bottom">IN BUSINESS</span></div>
  <p class="cta">ORDER NOW</p>
  <section class="ad__panel">
    <div class="panel__split"></div>
    <h3 class="product__title">SECURITY DOORS:</h3>
    <ul class="benefits"><li>3 Point Locking</li><li>Premium Mesh</li><li>Custom Made</li></ul>
    <p class="offer"><span class="offer__lead">FROM</span><span class="offer__value">$750</span></p>
  </section>
</article>

<!-- Blinds & Sheers -->
<article class="ad ad--sheer">
  <div class="ad__photo" role="img" aria-label="Room with floor-length grey sheer curtains drawn across a window"></div>
  <header class="ad__head">
    <div class="brand"><span class="brand__mark"></span><span class="brand__name">Portals Drapes<br>&amp; Louvres</span></div>
    <h2 class="ad__headline">SALE NOW ON</h2>
  </header>
  <p class="ad__address"><svg class="icon" viewBox="0 0 12 12"><circle cx="6" cy="6" r="6" fill="#fff"/><path d="M6 2.5a2 2 0 0 0-2 2c0 1.6 2 4 2 4s2-2.4 2-4a2 2 0 0 0-2-2z" fill="#E31E24"/></svg>482 Upper Wattleby Road, Kestrel Heights</p>
  <p class="ad__phone"><svg class="icon" viewBox="0 0 12 12"><circle cx="6" cy="6" r="6" fill="#fff"/><path d="M4 3.2l1 1.4-.6.7a4 4 0 0 0 2.3 2.3l.7-.6 1.4 1-.6 1A5.5 5.5 0 0 1 3 4z" fill="#0072BC"/></svg>9471 2658</p>
  <div class="badge"><span class="badge__top">CELEBRATING</span><span class="badge__num">13</span><span class="badge__years">YEARS</span><span class="badge__bottom">IN BUSINESS</span></div>
  <p class="cta">Book a FREE quote TODAY!</p>
  <section class="ad__panel">
    <h3 class="product__title">BLINDS &amp; SHEERS:</h3>
    <ul class="benefits"><li>Huge Range of Fabrics</li><li>Modern Soft Finish</li><li>Perfect for Any Room</li></ul>
    <p class="offer"><span class="offer__lead">UP TO</span><span class="offer__value">40% OFF</span></p>
  </section>
</article>

</body>
</html>
```